Youth Lifting Youth Business Card. We have existing logo

We need a business card design from an existing logo.
Our logo is in black and white but would love to add in the color burgundy but we're open to any color. Our website is www.youthliftingyouthmv.org

Target Market(s)

corporations and foundations who will be donating

Industry/Entity Type

Business

Contact Information for Business Card

Address: 2318 Marwick Ave Larkford, CA 95412
Name: Corin Halvorsen
Founder email: corin.halvorsen@youthliftingyouthmv.org
Phone: 805-637-9081

Requirements
Nice to have
• Our colors are burgundy and white, but that's not a necessity

```html
<!DOCTYPE html>
<html lang="en">
<head>
<meta charset="utf-8">
<title>Youth Lifting Youth – Business Card</title>
<link href="https://fonts.googleapis.com/css2?family=Tinos:ital,wght@0,400;0,700;1,400&display=swap" rel="stylesheet">
<style>
  :root{
    --backdrop:#e9e6e1;
    --card:#ffffff;
    --brand-red:#e3182a;
    --brand-red-dark:#c8101f;
    --accent-blue:#3a55a8;
    --ink:#111111;
    --photo-light:#f4f3f2;
    --photo-mid:#e6e2de;
  }
  *{box-sizing:border-box;margin:0;padding:0}
  html,body{width:1200px;height:848px;overflow:hidden;background:var(--backdrop)}
  body{display:flex;align-items:center;justify-content:center;font-family:"Tinos","Times New Roman",serif}
  .business-card{
    position:relative;width:980px;height:560px;background:var(--card);
    border-radius:22px;overflow:hidden;border-top:6px solid var(--accent-blue);
    box-shadow:0 18px 40px rgba(0,0,0,.18);
  }
  .photo-area{
    position:absolute;left:330px;top:160px;width:650px;height:300px;
    background:radial-gradient(ellipse at 60% 55%,var(--photo-mid) 0%,var(--photo-light) 55%,var(--card) 100%);
  }
  .bottom-band{
    position:absolute;left:0;right:0;bottom:0;height:100px;
    background:linear-gradient(var(--brand-red),var(--brand-red-dark));
  }
  .identity{position:absolute;left:230px;top:62px}
  .person-name{color:var(--brand-red);font-size:38px;font-weight:400;line-height:1}
  .person-title{color:var(--ink);font-size:18px;margin-top:2px}
  .person-phone{color:var(--accent-blue);font-size:22px;font-style:italic;margin-top:22px}
  .contact-list{position:absolute;left:218px;top:262px;list-style:none}
  .contact-item{display:flex;align-items:center;gap:12px;color:var(--accent-blue);font-size:24px;line-height:34px;white-space:nowrap}
  .contact-icon{width:26px;height:26px;flex:none}
  .org-mark{
    position:absolute;right:78px;top:66px;width:170px;height:170px;
    display:flex;align-items:center;justify-content:center;text-align:center;
  }
  .org-mark-circle{position:absolute;inset:0;border:3px solid var(--ink);border-radius:50%}
  .org-name{position:relative;color:var(--ink);font-size:21px;font-weight:400;line-height:1.15;width:130px}
</style>
</head>
<body>
  <article class="business-card">
    <div class="photo-area" role="img" aria-label="Faded photograph of smiling children resting their chins on their hands"></div>
    <div class="bottom-band"></div>

    <header class="identity">
      <h1 class="person-name">Corin Halvorsen</h1>
      <p class="person-title">Founder</p>
      <p class="person-phone">707-637-9081</p>
    </header>

    <ul class="contact-list">
      <li class="contact-item">
        <svg class="contact-icon" viewBox="0 0 26 26" aria-hidden="true">
          <rect width="26" height="26" rx="3" fill="#111"/>
          <rect x="5" y="8" width="16" height="11" fill="none" stroke="#e3182a" stroke-width="2"/>
          <path d="M5 8l8 6 8-6" fill="none" stroke="#e3182a" stroke-width="2"/>
        </svg>
        corin.halvorsen@youthliftingyouthmv.org
      </li>
      <li class="contact-item">
        <svg class="contact-icon" viewBox="0 0 26 26" aria-hidden="true">
          <rect width="26" height="26" rx="3" fill="#111"/>
          <path d="M13 5a5.5 5.5 0 0 0-5.5 5.5C7.5 15 13 21 13 21s5.5-6 5.5-10.5A5.5 5.5 0 0 0 13 5z" fill="#e3182a"/>
          <circle cx="13" cy="10.5" r="2" fill="#111"/>
        </svg>
        2318 Marwick Ave Larkford, CA 95412
      </li>
    </ul>

    <div class="org-mark">
      <span class="org-mark-circle"></span>
      <span class="org-name">Youth Lifting Youth Foundation</span>
    </div>
  </article>
</body>
</html>
```